Business Card Design

I already have a company logo for my company. I have a logo for the manufacturer we represent. I want a professional business card design.

```html
<!DOCTYPE html>
<html lang="en">
<head>
<meta charset="utf-8">
<title>Business Card – Beacon Alert Group</title>
<link href="https://fonts.googleapis.com/css2?family=Open+Sans:wght@400;600;700&display=swap" rel="stylesheet">
<style>
  :root {
    --bg: #232323;
    --card-light: #f4f4f4;
    --card-dark: #1e1e21;
    --red: #e3262b;
    --gold: #c0922b;
    --ink: #1f1f1f;
    --white: #ffffff;
  }
  * { margin: 0; padding: 0; box-sizing: border-box; }
  html, body {
    width: 1200px; height: 780px; overflow: hidden;
    background: var(--bg);
    font-family: "Open Sans", Arial, sans-serif;
  }
  .canvas {
    position: relative; width: 1200px; height: 780px;
  }
  .card {
    position: absolute; top: 235px;
    width: 540px; height: 310px;
    border-radius: 4px;
    box-shadow: 0 10px 30px rgba(0,0,0,.45);
    overflow: hidden;
  }
  .card-front { left: 40px; background: var(--card-light); }
  .card-back { left: 620px; background: var(--card-dark); }

  .front-sweep {
    position: absolute; left: 150px; top: 90px;
    width: 300px; height: 150px;
    background: linear-gradient(160deg, rgba(0,0,0,0) 40%, rgba(0,0,0,.12) 70%, rgba(0,0,0,0) 100%);
    border-radius: 0 0 0 100%;
    transform: skewX(-25deg);
  }
  .holder-name {
    position: absolute; left: 58px; top: 52px;
    font-size: 30px; font-weight: 700; letter-spacing: -.3px;
  }
  .holder-name .first { color: var(--red); }
  .holder-name .last { color: var(--gold); }
  .holder-title {
    position: absolute; left: 140px; top: 96px;
    font-size: 15px; font-weight: 600; color: var(--ink);
  }
  .contact-list {
    position: absolute; left: 280px; top: 140px;
    list-style: none;
  }
  .contact-list li {
    display: flex; align-items: center; gap: 8px;
    font-size: 15px; font-weight: 600; color: var(--ink);
    line-height: 24px;
  }
  .contact-list svg { width: 14px; height: 14px; flex: none; }
  .holder-address {
    position: absolute; left: 58px; top: 250px;
    font-size: 15px; font-weight: 600; color: var(--ink);
  }

  .brand {
    position: absolute; right: 34px; bottom: 40px;
    display: flex; align-items: center; gap: 10px;
  }
  .brand-mark { width: 18px; height: 18px; background: var(--red); }
  .brand-name {
    font-size: 20px; font-weight: 700; color: var(--white);
    letter-spacing: 1px; text-transform: uppercase;
  }
</style>
</head>
<body>
<div class="canvas">
  <section class="card card-front">
    <div class="front-sweep"></div>
    <h1 class="holder-name"><span class="first">Marta</span> <span class="last">Velinska</span></h1>
    <p class="holder-title">Managing Director</p>
    <ul class="contact-list">
      <li>
        <svg viewBox="0 0 24 24" aria-hidden="true"><path fill="#e3262b" d="M6.6 10.8a15.1 15.1 0 0 0 6.6 6.6l2.2-2.2c.3-.3.7-.4 1-.2 1.1.4 2.3.6 3.6.6.6 0 1 .4 1 1V20c0 .6-.4 1-1 1A17 17 0 0 1 3 4c0-.6.4-1 1-1h3.5c.6 0 1 .4 1 1 0 1.3.2 2.5.6 3.6.1.3 0 .7-.2 1z"/></svg>
        (555) 214-6083
      </li>
      <li>
        <svg viewBox="0 0 24 24" aria-hidden="true"><rect x="2" y="5" width="20" height="14" rx="2" fill="#e3262b"/><path d="M3 6l9 7 9-7" fill="none" stroke="#fff" stroke-width="2"/></svg>
        hello@beaconalert.com
      </li>
      <li>
        <svg viewBox="0 0 24 24" aria-hidden="true"><circle cx="12" cy="12" r="10" fill="#e3262b"/><path d="M2 12h20M12 2c3 3 3 17 0 20M12 2c-3 3-3 17 0 20" fill="none" stroke="#fff" stroke-width="1.5"/></svg>
        www.beaconalert.com
      </li>
    </ul>
    <p class="holder-address">4180 Linden Ave. Suite 310 Carver City, TX 75500</p>
  </section>

  <section class="card card-back">
    <div class="brand">
      <span class="brand-mark"></span>
      <span class="brand-name">Beacon Alert Group</span>
    </div>
  </section>
</div>
</body>
</html>
```